Client Centric Brochure for Investment Advisory Firm

We need a client centric firm brochure that not only spotlights the services we provide as a wealth and investment management firm but also the value our expertise and expierience brings. We would like see designs that use this particular color green (RGB-0,92,51) and variations. Shouldn't be limited to this color however and are open to other color schemes Looking for something clean and consise. The final design should communicate financial safety, growth and reaching investment goals. Attached are rudimentary designs we have created, our company logo, and other source material. You can also visit our website www.tallowbrookfunds.com for more inspiration.

Target Market(s)

Age Range - 35-65, Gender - 70% male, 30% female, Those looking to secure their financial future through wealth management and investing.

Industry/Entity Type

Investment

Font styles to use
Serif
Sans Serif

Colors
00a990

Requirements
Must have
• Project must have some of the information that was provided in the source documents. It must exhibit the client centric nature we are trying to exude.

```html
<!DOCTYPE html>
<html lang="en">
<head>
<meta charset="utf-8">
<title>Tallowbrook Funds – Inside Spread</title>
<link rel="stylesheet" href="https://fonts.googleapis.com/css2?family=Exo+2:wght@400;700&family=Raleway:wght@400;500;700&display=swap">
<style>
  :root {
    --green-deep: #0b5a3f;
    --green-ink: #12493a;
    --green-mid: #2f7d68;
    --green-soft: #6ea08f;
    --green-night: #062b1e;
    --paper: #f4f5f4;
    --paper-shade: #dcdedd;
    --text: #2b3a35;
    --stage: #ffffff;
  }
  * { box-sizing: border-box; margin: 0; padding: 0; }
  html, body { width: 1200px; height: 685px; overflow: hidden; background: var(--stage); }
  body { font-family: "Raleway", sans-serif; color: var(--text); }

  .spread {
    position: absolute; left: 0; top: 68px;
    width: 1426px; height: 652px;
    transform: scale(0.8415); transform-origin: 0 0;
    overflow: hidden;
  }
  .panel { position: absolute; top: 0; height: 652px; overflow: hidden; }
  .panel--left { left: 0; width: 475px; background: linear-gradient(135deg, #ffffff 30%, var(--paper-shade)); }
  .panel--middle { left: 475px; width: 475px; }
  .panel--right { left: 950px; width: 476px; }
  .panel--middle .backdrop, .panel--right .backdrop {
    position: absolute; inset: 0;
    background: linear-gradient(180deg, #f7f8f7 0%, #e2e6e4 45%, #cfd6d3 100%);
  }
  .shapes { position: absolute; left: 0; top: 0; width: 1426px; height: 652px; }

  .heading { font-family: "Exo 2", sans-serif; color: var(--green-ink); line-height: 1.1; }
  .heading strong { font-weight: 700; display: block; }
  .heading span { font-weight: 400; display: block; }
  .heading-rule { height: 3px; background: var(--green-deep); margin-top: 6px; }

  .about-heading { position: absolute; left: 27px; top: 323px; }
  .about-heading strong { font-size: 22px; letter-spacing: 1px; }
  .about-heading span { font-size: 20px; }
  .about-heading .heading-rule { width: 190px; height: 2px; }
  .about-copy {
    position: absolute; left: 27px; top: 397px; width: 422px;
    font-size: 10.5px; line-height: 19px; text-align: justify;
  }
  .about-copy .initial { font-size: 24px; color: #666; line-height: 0; }

  .think-heading { position: absolute; right: 33px; top: 32px; text-align: right; }
  .think-heading strong { font-size: 23px; letter-spacing: 1px; }
  .think-heading span { font-size: 20px; }
  .think-heading .heading-rule { width: 106px; margin-left: auto; }
  .think-copy {
    position: absolute; left: 187px; top: 110px; width: 256px;
    font-size: 10.3px; line-height: 17px; text-align: justify;
  }
  .advantages {
    position: absolute; left: 215px; top: 288px; list-style: none;
    font-size: 11px; font-weight: 700; line-height: 16px; color: var(--green-ink);
    border-left: 1px solid var(--text); padding-left: 12px;
  }
  .advantages li::before { content: "●"; font-size: 8px; margin: 0 6px 0 -6px; vertical-align: 1px; }
  .further-copy {
    position: absolute; left: 25px; top: 375px; width: 418px;
    font-size: 10px; line-height: 16px; text-align: justify;
  }
  .signing-photo {
    position: absolute; left: 25px; top: 442px; width: 133px; height: 118px;
    border: 4px solid #fff;
    background: linear-gradient(135deg, #d9b5c7, #7a3a5c 55%, #c6a1b3);
  }
  .etf-rule { position: absolute; left: 180px; top: 442px; width: 263px; height: 2px; background: var(--green-deep); }
  .etf-copy {
    position: absolute; left: 180px; top: 458px; width: 263px;
    font-size: 10px; line-height: 16px; text-align: justify;
  }

  .experience-heading { position: absolute; left: 23px; top: 36px; }
  .experience-heading span { font-size: 20px; }
  .experience-heading strong { font-size: 22px; letter-spacing: 0.5px; }
  .experience-heading .heading-rule { width: 179px; }
  .experience-copy {
    position: absolute; left: 25px; width: 423px;
    font-size: 9.8px; line-height: 17px; text-align: justify;
  }
  .experience-copy--one { top: 108px; }
  .experience-copy--two { top: 210px; }
  .etf-heading { position: absolute; left: 23px; top: 338px; }
  .etf-heading span { font-size: 20px; }
  .etf-heading strong { font-size: 23px; letter-spacing: 1px; }
  .etf-heading .heading-rule { width: 98px; }
  .etf-benefits {
    position: absolute; left: 27px; top: 407px; width: 240px; list-style: none;
    font-size: 10px; line-height: 17px;
  }
  .etf-benefits li { margin-bottom: 4px; padding-left: 12px; position: relative; }
  .etf-benefits li::before { content: "●"; position: absolute; left: 0; font-size: 7px; }
  .station-photo { position: absolute; left: 0; top: 0; }

  .brand {
    position: absolute; left: 20px; top: 602px;
    display: flex; align-items: center; gap: 8px;
    font-family: "Raleway", sans-serif; font-weight: 500; font-size: 17px; color: var(--green-ink);
  }
  .brand-mark { width: 16px; height: 16px; background: var(--green-mid); }
  .web-band {
    position: absolute; left: 190px; top: 613px; width: 290px; height: 19px;
    background: var(--green-night);
    clip-path: polygon(16px 0, 100% 0, 100% 100%, 0 100%);
    color: #fff; font-size: 11.5px; letter-spacing: 1px; line-height: 19px;
    padding-left: 50px;
  }
  .accent-band {
    position: absolute; left: 0; top: 632px; width: 210px; height: 20px;
    background: var(--green-soft);
    clip-path: polygon(0 0, 190px 0, 100% 100%, 0 100%);
  }
  .base-band { position: absolute; left: 0; top: 632px; width: 100%; height: 20px; background: #ececec; }
</style>
</head>
<body>
<main class="spread">

  <section class="panel panel--left">
    <div class="about-heading heading">
      <strong>ABOUT</strong>
      <span>Tallowbrook Funds</span>
      <div class="heading-rule"></div>
    </div>
    <p class="about-copy"><span class="initial">T</span>allowbrook Funds provides investment guidance to clients based on their specific financial objectives. In addressing client objectives, we consider risk tolerance, time horizon, income needs, liquidity needs, tax sensitivity, and other pertinent factors. Investment strategies include taxable and tax-exempt fixed income strategies, and diversified portfolio strategies for conservative, moderate, and aggressive investors. All investment strategies seek to provide an appropriate balance between risk and reward. All strategies strive to deliver sophisticated investment solutions focused on meeting each client's needs.</p>
    <div class="base-band"></div>
    <div class="accent-band"></div>
    <div class="brand"><span class="brand-mark"></span>Tallowbrook</div>
    <div class="web-band">www.tallowbrookfunds.com</div>
  </section>

  <section class="panel panel--middle">
    <div class="backdrop" role="img" aria-label="Faded city skyline of office towers"></div>
    <div class="think-heading heading">
      <strong>We Think</strong>
      <span>Differently</span>
      <div class="heading-rule"></div>
    </div>
    <p class="think-copy">Tallowbrook Funds offers three distinct, yet complementary categories of investment solutions to address client needs across any market environment: Income, Growth and Focused. The majority of our proprietary family of portfolios within each of these broad categories are built with Exchange-Traded Funds (ETFs) to deliver distinct advantages over both traditional stocks-and-bonds investing, advantages such as:</p>
    <ul class="advantages">
      <li>Broader diversification</li>
      <li>Greater focus on asset allocation</li>
      <li>Passive vs. active management</li>
      <li>Lowers costs</li>
    </ul>
    <p class="further-copy">Further, they are tailored to address the new, complex realities of today's financial markets. In a global investment environment characterized by increased volatility, we help our clients succeed by managing what is within their control.</p>
    <div class="signing-photo" role="img" aria-label="Close-up of a hand signing a document with a pen, tinted plum"></div>
    <div class="etf-rule"></div>
    <p class="etf-copy">ETFs offer advantages over individual securities, mutual funds and static index investing that can significantly enhance portfolio performance. They are highly-efficient investment vehicles that can replace stocks, stock funds, bonds, bond funds, index funds, and more.</p>
    <div class="base-band"></div>
    <div class="accent-band"></div>
    <div class="brand"><span class="brand-mark"></span>Tallowbrook</div>
    <div class="web-band">www.tallowbrookfunds.com</div>
  </section>

  <section class="panel panel--right">
    <div class="backdrop" role="img" aria-label="Faded view of glass office towers"></div>
    <svg class="station-photo" width="476" height="652" viewBox="0 0 476 652">
      <defs>
        <linearGradient id="stationTone" x1="0" y1="0" x2="1" y2="1">
          <stop offset="0" stop-color="#bcd3c9"/>
          <stop offset="0.5" stop-color="#6f9a88"/>
          <stop offset="1" stop-color="#2f5d4c"/>
        </linearGradient>
      </defs>
      <polygon points="270,470 400,362 476,358 476,652 230,652 190,560" fill="url(#stationTone)" role="img" aria-label="Green-tinted photo of a busy train station platform"/>
      <polygon points="265,478 400,358 428,358 420,368 285,478" fill="var(--green-mid)"/>
    </svg>
    <div class="experience-heading heading">
      <span>Benefit from</span>
      <strong>Our Experience</strong>
      <div class="heading-rule"></div>
    </div>
    <p class="experience-copy experience-copy--one">At Tallowbrook Funds, we understand the many challenges of today's economic environment. Growing complexity around the globe makes the need for investment advice more critical than ever. Investors today are seeking new solutions that can help them navigate market risks, remain nimble in a changing global economy, and feel confident about their futures.</p>
    <p class="experience-copy experience-copy--two">The Tallowbrook family of investment portfolios are managed by an experienced portfolio management team who conduct independent research and security analysis. The main objective of our portfolio managers is to maximize the return of your investment with the level of measured risk that is consistent with your personal or business investor profile. We aim to deliver the best possible performance through all market cycles.</p>
    <div class="etf-heading heading">
      <span>Benefit of</span>
      <strong>ETFS</strong>
      <div class="heading-rule"></div>
    </div>
    <ul class="etf-benefits">
      <li>Are low cost, tax efficient and transparent</li>
      <li>Offer liquidity and trading flexibility</li>
      <li>Allow for diversification with asset classes and by geography</li>
      <li>Employ tactical risk management</li>
    </ul>
    <div class="base-band"></div>
    <div class="accent-band"></div>
    <div class="brand"><span class="brand-mark"></span>Tallowbrook</div>
    <div class="web-band">www.tallowbrookfunds.com</div>
  </section>

  <svg class="shapes" viewBox="0 0 1426 652">
    <defs>
      <linearGradient id="teamTone" x1="0" y1="0" x2="1" y2="1">
        <stop offset="0" stop-color="#4f7a68"/>
        <stop offset="0.5" stop-color="#9fbcae"/>
        <stop offset="1" stop-color="#244a3c"/>
      </linearGradient>
    </defs>
    <polygon points="0,0 600,0 612,150 590,200 520,240 290,305 255,305 0,70" fill="url(#teamTone)" role="img" aria-label="Green-tinted photo of three smiling portfolio managers in suits"/>
    <polygon points="0,62 0,92 245,310 262,306" fill="var(--green-deep)"/>
    <polygon points="590,0 640,0 625,120 590,175 400,285 400,265 570,170 600,120" fill="var(--green-mid)"/>
  </svg>

</main>
</body>
</html>
```